Cover for Lanterns Along the Quiet Shore of Being

Cover for a book that describes everything that happens to a person, from pre-birth life plans through growing in compassion and wisdom to death and living in the afterlife. The information is revealed in messages from people living in the life after this life. The title is Lessons Gathered From Every Season of Your Existence: Shared by Voices Dwelling Beyond the Veil. Author is T. Wesley Prandt. Book size is 6 by 9.

Target Market(s)

General

Font styles to use
Serif

```html
<!DOCTYPE html>
<html lang="en">
<head>
<meta charset="utf-8">
<title>Lessons Gathered From Every Season of Your Existence — T. Wesley Prandt</title>
<link rel="stylesheet" href="https://fonts.googleapis.com/css2?family=Cormorant+Garamond:wght@500;600&family=Great+Vibes&family=Crimson+Text&display=swap">
<style>
  :root {
    --blue-deep: #0d5aa3;
    --blue-mid: #1c84c6;
    --blue-glow: #33a6d8;
    --ink-light: #ffffff;
    --figure-tone: #eef3f6;
  }
  * { margin: 0; padding: 0; box-sizing: border-box; }
  html, body { width: 845px; height: 1200px; overflow: hidden; }
  body { background: var(--blue-deep); }

  .cover {
    position: relative;
    width: 845px;
    height: 1200px;
    overflow: hidden;
    color: var(--ink-light);
    font-family: "Cormorant Garamond", Georgia, serif;
    font-weight: 500;
    text-align: center;
    background:
      radial-gradient(ellipse 60% 45% at 55% 55%, var(--blue-glow) 0%, rgba(51,166,216,0) 70%),
      radial-gradient(ellipse 90% 80% at 50% 45%, var(--blue-mid) 0%, var(--blue-deep) 100%);
  }

  .title-line {
    position: absolute;
    left: 0;
    width: 100%;
    line-height: 1;
    text-transform: uppercase;
  }
  .title-main { top: 88px; font-size: 128px; letter-spacing: 2px; }
  .title-bridge {
    display: flex;
    align-items: center;
    justify-content: center;
    gap: 18px;
    font-size: 50px;
  }
  .title-bridge::before,
  .title-bridge::after {
    content: "";
    display: block;
    height: 2px;
    background: var(--ink-light);
  }
  .bridge-one { top: 208px; }
  .bridge-one::before, .bridge-one::after { width: 150px; }
  .bridge-two { top: 352px; }
  .bridge-two::before, .bridge-two::after { width: 170px; }
  .title-mid { top: 268px; font-size: 76px; }
  .title-close { top: 438px; font-size: 76px; }

  .figure-area {
    position: absolute;
    left: 253px;
    top: 602px;
    width: 354px;
    height: 396px;
  }

  .author {
    position: absolute;
    left: 0;
    top: 1010px;
    width: 100%;
    font-family: "Great Vibes", cursive;
    font-weight: 400;
    font-size: 84px;
    line-height: 1;
  }

  .subtitle {
    position: absolute;
    left: 0;
    top: 1150px;
    width: 100%;
    font-family: "Crimson Text", Georgia, serif;
    font-size: 28px;
    line-height: 1;
  }
</style>
</head>
<body>
  <main class="cover">
    <h1>
      <span class="title-line title-main">Lessons</span>
      <span class="title-line title-bridge bridge-one">Gathered From</span>
      <span class="title-line title-mid">Every Season</span>
      <span class="title-line title-bridge bridge-two">Of Your</span>
      <span class="title-line title-close">Existence</span>
    </h1>

    <svg class="figure-area" viewBox="0 0 354 396" role="img" aria-label="White silhouette of a woman leaping upward with arms and hair flowing back">
      <defs>
        <radialGradient id="figureGlow" cx="50%" cy="50%" r="50%">
          <stop offset="0%" stop-color="#eef3f6" stop-opacity="0.55"/>
          <stop offset="100%" stop-color="#eef3f6" stop-opacity="0"/>
        </radialGradient>
      </defs>
      <rect width="354" height="396" fill="url(#figureGlow)"/>
    </svg>

    <p class="author">T. Wesley Prandt</p>
    <p class="subtitle">Shared by Voices Dwelling Beyond the Veil</p>
  </main>
</body>
</html>
```